Design Cloud for Core Values & Attributes

See Image Example Below "Word Cloud" this is what we would like this to look like.
The second image is all of the Core Value and Attributes I will list below.
CORE VALUES need to be the bigger words (based off the image I sent) Capitalized, BOLD, Navy
Independence, Capitalism, Trust, Fun, Safety, Growth
ATTRIBUTES need to be the smaller words, lower case, non-bold, lighter blue mixed in (based off the image I sent):
Humility, Consistency, Open Mindedness, Curiosity, Selflessness, Caring, Conscientiousness, Honorable, Cunning, Competitive, Compartmentalization, Innovative, Perseverance, Authenticity, Decisiveness, Self-efficacy, Accountability, Generosity, Humor, Optimism, Resilience, Inclusive, Insouciance to what others think, Courage, Decisive, Curious, Integrity

```html
<!DOCTYPE html>
<html lang="en">
<head>
<meta charset="utf-8">
<title>Core Value Word Cloud</title>
<link rel="stylesheet" href="https://fonts.googleapis.com/css2?family=Montserrat:wght@400;700;800&display=swap">
<style>
  :root {
    --backdrop: #e4e4e4;
    --paper-light: #ffffff;
    --paper-shade: #eeeff1;
    --navy: #0052a5;
    --attribute-blue: #1a6fb6;
  }
  html, body {
    margin: 0;
    padding: 0;
    width: 1200px;
    height: 1200px;
    overflow: hidden;
    background: var(--backdrop);
  }
  .word-cloud {
    position: absolute;
    left: 0;
    top: 176px;
    width: 1200px;
    height: 848px;
    display: block;
  }
  .core-value {
    font-family: "Montserrat", sans-serif;
    font-weight: 700;
    font-size: 68px;
    fill: var(--navy);
  }
  .core-value--headline {
    font-weight: 800;
    font-size: 172px;
  }
  .attribute {
    font-family: "Montserrat", sans-serif;
    font-weight: 400;
    font-size: 45px;
    fill: var(--attribute-blue);
  }
</style>
</head>
<body>
<svg class="word-cloud" viewBox="0 0 1596 1128" xmlns="http://www.w3.org/2000/svg" role="img" aria-label="Core value word cloud">
  <defs>
    <linearGradient id="paper-gradient" x1="0" y1="0" x2="1" y2="1">
      <stop offset="0" stop-color="var(--paper-light)"/>
      <stop offset="0.5" stop-color="var(--paper-shade)"/>
      <stop offset="1" stop-color="var(--paper-light)"/>
    </linearGradient>
  </defs>
  <rect class="paper" width="1596" height="1128" fill="url(#paper-gradient)"/>

  <g class="headline">
    <text class="core-value core-value--headline" x="288" y="458" textLength="488" lengthAdjust="spacingAndGlyphs">CORE</text>
    <text class="core-value core-value--headline" x="487" y="608" textLength="589" lengthAdjust="spacingAndGlyphs">VALUE</text>
  </g>

  <g class="core-values">
    <text class="core-value" x="510" y="168" textLength="154" lengthAdjust="spacingAndGlyphs">Trust</text>
    <text class="core-value" transform="translate(729 258) rotate(-90)" x="0" y="0" textLength="105" lengthAdjust="spacingAndGlyphs">Fun</text>
    <text class="core-value" x="797" y="391" textLength="334" lengthAdjust="spacingAndGlyphs">Capitalism</text>
    <text class="core-value" x="797" y="460" textLength="201" lengthAdjust="spacingAndGlyphs">Safety</text>
    <text class="core-value" x="315" y="676" textLength="450" lengthAdjust="spacingAndGlyphs">Independence</text>
    <text class="core-value" x="848" y="890" textLength="238" lengthAdjust="spacingAndGlyphs">Growth</text>
  </g>

  <g class="attributes">
    <text class="attribute" x="452" y="214" textLength="212" lengthAdjust="spacingAndGlyphs">OPTIMISM</text>
    <text class="attribute" x="348" y="260" textLength="316" lengthAdjust="spacingAndGlyphs">DECISIVENESS</text>
    <text class="attribute" x="163" y="316" textLength="575" lengthAdjust="spacingAndGlyphs">COMPARTMENTALIZATION</text>
    <text class="attribute" transform="translate(784 316) rotate(-90)" x="0" y="0" textLength="203" lengthAdjust="spacingAndGlyphs">CUNNING</text>
    <text class="attribute" x="809" y="143" textLength="231" lengthAdjust="spacingAndGlyphs">INTEGRITY</text>
    <text class="attribute" x="807" y="188" textLength="282" lengthAdjust="spacingAndGlyphs">GENEROSITY</text>
    <text class="attribute" x="810" y="234" textLength="295" lengthAdjust="spacingAndGlyphs">COMPETITIVE</text>
    <text class="attribute" x="810" y="281" textLength="328" lengthAdjust="spacingAndGlyphs">SELFLESSNESS</text>
    <text class="attribute" x="807" y="329" textLength="355" lengthAdjust="spacingAndGlyphs">PERSEVERANCE</text>
    <text class="attribute" x="1013" y="460" textLength="384" lengthAdjust="spacingAndGlyphs">ACCOUNTABILITY</text>
    <text class="attribute" x="267" y="510" textLength="197" lengthAdjust="spacingAndGlyphs">HUMILITY</text>
    <text class="attribute" x="1093" y="510" textLength="217" lengthAdjust="spacingAndGlyphs">COURAGE</text>
    <text class="attribute" x="266" y="563" textLength="200" lengthAdjust="spacingAndGlyphs">DECISIVE</text>
    <text class="attribute" x="1093" y="563" textLength="162" lengthAdjust="spacingAndGlyphs">HUMOR</text>
    <text class="attribute" transform="translate(1307 721) rotate(-90)" x="0" y="0" textLength="195" lengthAdjust="spacingAndGlyphs">CURIOUS</text>
    <text class="attribute" x="216" y="615" textLength="282" lengthAdjust="spacingAndGlyphs">HONORABLE</text>
    <text class="attribute" x="1093" y="613" textLength="171" lengthAdjust="spacingAndGlyphs">CARING</text>
    <text class="attribute" x="786" y="676" textLength="477" lengthAdjust="spacingAndGlyphs">CONSCIENTIOUSNESS</text>
    <text class="attribute" x="389" y="728" textLength="870" lengthAdjust="spacingAndGlyphs">INSOUCIANCE TO WHAT OTHERS THINK</text>
    <text class="attribute" x="532" y="782" textLength="234" lengthAdjust="spacingAndGlyphs">CURIOSITY</text>
    <text class="attribute" x="846" y="778" textLength="253" lengthAdjust="spacingAndGlyphs">RESILIENCE</text>
    <text class="attribute" x="538" y="830" textLength="228" lengthAdjust="spacingAndGlyphs">INCLUSIVE</text>
    <text class="attribute" x="848" y="830" textLength="425" lengthAdjust="spacingAndGlyphs">OPEN MINDEDNESS</text>
    <text class="attribute" x="455" y="878" textLength="311" lengthAdjust="spacingAndGlyphs">CONSISTENCY</text>
    <text class="attribute" x="444" y="925" textLength="322" lengthAdjust="spacingAndGlyphs">AUTHENTICITY</text>
    <text class="attribute" x="423" y="973" textLength="343" lengthAdjust="spacingAndGlyphs">SELF-EFFICACY</text>
    <text class="attribute" transform="translate(824 1016) rotate(-90)" x="0" y="0" textLength="263" lengthAdjust="spacingAndGlyphs">INNOVATIVE</text>
  </g>
</svg>
</body>
</html>
```